Website for new child psychology practice

New clinical psychology practice in NSW Australia, specialising in work with children, adolescents and families. I would like to feature the colours in the logo, which was recently designed by pixelharbor designer Odette.
I am seeking a professional looking page, which is easy to navigate and is colourful and playful but not childish.
Target Market(s)
Parents and professionals
Industry/Entity Type
Health
Coding
Coded - Design and coding required
Number of Pages Required
1 page
Font styles to use
Serif
Requirements
Must have
- Pages for 'About us' 'Services' 'Fees and information' 'Contact us'
Should not have
- Childish stock photos

```html
<!DOCTYPE html>
<html lang="en">
<head>
<meta charset="utf-8">
<title>Dr Clara Webb – Clinical Psychologist</title>
<link href="https://fonts.googleapis.com/css2?family=Cinzel:wght@400;600;700&family=Roboto:wght@400;500&display=swap" rel="stylesheet">
<style>
:root{
  --plum:#7b1767;
  --plum-light:#a02a8a;
  --plum-deep:#5e0f4e;
  --ink:#141414;
  --text:#444;
  --muted:#666;
  --line:#d8d8d8;
  --panel:#f3f3f3;
  --white:#fff;
  --black:#000;
}
*{box-sizing:border-box;margin:0;padding:0}
html,body{width:1200px;height:3297px;overflow:hidden;background:var(--white)}
body{font-family:'Roboto',sans-serif;color:var(--text);position:relative}
.serif{font-family:'Cinzel',serif}
.abs{position:absolute}
.btn{display:inline-block;background:linear-gradient(180deg,var(--plum-light),var(--plum));color:var(--white);font-family:'Cinzel',serif;font-weight:700;font-size:17px;border-radius:26px;box-shadow:0 4px 8px rgba(0,0,0,.18);text-align:center}
.kicker{font-family:'Cinzel',serif;font-size:22px;color:var(--ink);display:flex;align-items:center;gap:10px}
.kicker::before,.kicker::after{content:"";width:37px;height:2px;background:currentColor}

/* header */
.site-header{top:0;left:0;width:1200px;height:86px;background:var(--white)}
.brand{left:98px;top:22px;display:flex;align-items:center;gap:10px}
.brand-dot{width:40px;height:40px;border-radius:50%;background:var(--plum)}
.brand-name{font-family:'Cinzel',serif;font-weight:600;font-size:24px;color:var(--ink);line-height:1}
.brand-sub{font-family:'Cinzel',serif;font-weight:600;font-size:10px;letter-spacing:2px;color:var(--ink);margin-top:3px}
.nav{left:474px;top:37px;display:flex;gap:24px;font-family:'Cinzel',serif;font-size:15px;color:var(--ink)}
.nav .active{color:var(--plum);font-weight:700;text-decoration:underline;text-underline-offset:4px}
.nav-cta{left:960px;top:19px;width:141px;height:48px;line-height:48px}

/* hero */
.hero{top:86px;left:0;width:1200px;height:599px;background:linear-gradient(90deg,#e9e6e2 0%,#dcd6cf 45%,#b8b0a8 70%,#d6d3d0 100%)}
.hero-title{left:98px;top:262px;font-family:'Cinzel',serif;font-weight:700;font-size:46px;line-height:64px;color:var(--ink)}
.hero-text{left:99px;top:402px;font-size:17px;color:var(--ink)}
.hero-btn{left:98px;top:447px;width:150px;height:49px;line-height:49px}

/* about */
.about-arc{left:42px;top:900px}
.about-frame{left:108px;top:811px;width:478px;height:448px;border:3px solid var(--plum);border-top:0;border-left:0}
.about-frame::before{content:"";position:absolute;left:0;bottom:0;width:3px;height:20px;background:var(--plum)}
.about-photo{left:98px;top:801px;width:474px;height:444px;background:linear-gradient(135deg,#b99782,#8d8f86 50%,#5d6068);box-shadow:0 4px 12px rgba(0,0,0,.15)}
.section-title{font-family:'Cinzel',serif;font-weight:700;font-size:38px;color:var(--ink)}
.about-title{left:634px;top:794px}
.about-kicker{left:634px;top:856px}
.about-copy{left:634px;top:898px;width:466px;font-size:15px;line-height:31px;color:var(--muted)}
.about-btn{left:634px;top:1194px;width:141px;height:48px;line-height:48px}

/* services */
.services{top:1357px;left:0;width:1200px;height:694px;background:linear-gradient(180deg,var(--plum-deep) 0%,#7e1c6c 45%,#a0418f 100%)}
.services-title{left:103px;top:1456px;color:var(--white)}
.services-kicker{left:100px;top:1518px;color:var(--white)}
.services-divider{left:428px;top:1460px;width:3px;height:86px;background:var(--white)}
.services-copy{left:474px;top:1454px;width:626px;font-size:15px;line-height:31px;color:var(--white)}
.card{top:1614px;width:317px;height:337px;background:var(--white);border-radius:4px}
.card-icon{position:absolute;left:30px;top:33px;width:48px;height:48px;border-radius:8px;background:#e6c9df}
.card-title{position:absolute;left:30px;top:108px;font-family:'Cinzel',serif;font-weight:700;font-size:19px;letter-spacing:1px;color:var(--ink)}
.card hr{position:absolute;left:0;top:154px;width:100%;border:0;border-top:2px solid var(--line)}
.card-text{position:absolute;left:24px;top:170px;width:275px;font-size:15px;line-height:31px;color:var(--muted)}
.card-link{position:absolute;left:28px;top:285px;font-family:'Cinzel',serif;font-weight:700;font-size:16px;color:var(--ink);display:flex;align-items:center;gap:12px}

/* fees */
.fees-title{left:0;top:2133px;width:1200px;text-align:center}
.fees-kicker{left:0;top:2200px;width:1200px;justify-content:center}
.fees-copy{left:160px;top:2244px;width:880px;text-align:center;font-size:15px;line-height:31px;color:var(--ink)}
.fees-photo{left:141px;top:2340px;width:688px;height:340px;background:linear-gradient(120deg,#c9b3a1,#e8e2d8 50%,#9db28a 75%,#6a6763)}
.fees-panel{left:699px;top:2391px;width:361px;height:342px;background:var(--panel);box-shadow:0 2px 8px rgba(0,0,0,.12)}
.fees-panel h3{position:absolute;left:28px;top:43px;font-family:'Cinzel',serif;font-weight:700;font-size:21px;letter-spacing:1px;color:var(--ink)}
.fees-list{position:absolute;left:28px;top:85px;list-style:none}
.fees-list li{display:flex;align-items:center;gap:16px;height:45px;font-size:17px;color:var(--ink)}
.fees-list li::before{content:"";width:28px;height:28px;border-radius:50%;background:radial-gradient(circle,var(--plum-light) 35%,#e3b6d6 36%)}

/* footer */
.footer{top:2850px;left:0;width:1200px;height:447px;background:var(--black);color:var(--white)}
.footer h4{font-family:'Cinzel',serif;font-weight:700;font-size:22px;letter-spacing:1px}
.quick{left:98px;top:2920px}
.quick ul{list-style:none;margin-top:14px}
.quick li{display:flex;align-items:center;gap:12px;font-size:15px;height:31px}
.social{left:98px;top:3126px;display:flex;gap:8px}
.social span{width:30px;height:30px;border-radius:50%;background:var(--plum)}
.vline{top:2940px;width:0;height:240px;border-left:1px dashed #888}
.contact{left:355px;top:2920px;width:240px}
.contact-item{display:flex;gap:14px;padding:14px 0;border-bottom:1px dashed #888}
.contact-item:last-child{border:0}
.contact-icon{flex:0 0 32px;height:32px;border-radius:50%;background:var(--plum);display:flex;align-items:center;justify-content:center}
.contact-item b{display:block;font-size:16px;font-weight:500;line-height:28px}
.contact-item p{font-size:15px;line-height:31px}
.form{left:716px;top:2920px;width:353px}
.field{height:40px;border:1px solid #bbb;border-radius:3px;margin-top:13px;padding:0 12px;line-height:38px;font-size:15px}
.form h4{margin-bottom:7px}
.submit{margin-top:15px;height:38px;line-height:38px;text-align:center;background:linear-gradient(180deg,var(--plum-light),var(--plum));font-family:'Cinzel',serif;font-weight:700;font-size:18px;border-radius:3px}
.footer-rule{left:98px;top:3240px;width:1003px;border-top:1px solid #666}
.copyright{left:0;top:3262px;width:1200px;text-align:center;font-size:15px}
</style>
</head>
<body>

<header class="site-header abs">
  <div class="brand abs">
    <span class="brand-dot"></span>
    <div><div class="brand-name">Dr Clara Webb</div><div class="brand-sub">Clinical Psychologist</div></div>
  </div>
  <nav class="nav abs"><span class="active">Home</span><span>About Us</span><span>Services</span><span>Fees and Information</span></nav>
  <a class="btn nav-cta abs">Contact Us</a>
</header>

<section class="hero abs" role="img" aria-label="Photo of a smiling psychologist in a light office talking with a client"></section>
<h1 class="hero-title abs">Welcome To<br>Dr.Clara Webb</h1>
<p class="hero-text abs">Clinical psychology practice in NSW Australia</p>
<a class="btn hero-btn abs">Get Started</a>

<svg class="about-arc abs" width="160" height="160" viewBox="0 0 160 160"><path d="M62 5 A75 75 0 0 0 62 155" fill="none" stroke="var(--plum)" stroke-width="10"/></svg>
<div class="about-frame abs"></div>
<div class="about-photo abs" role="img" aria-label="Photo of a psychologist seated on a sofa holding a notebook"></div>
<h2 class="section-title about-title abs">About Us</h2>
<div class="kicker about-kicker abs">Who We Are</div>
<p class="about-copy abs">Lorem ipsum dolor sit amet, consectetur adipiscing elit, sed do eiusmod tempor incididunt ut labore et dolore magna aliqua. Ut enim ad minim veniam, quis nostrud exercitation ullamco laboris nisi ut aliquip ex ea commodo consequat. Duis aute irure dolor in reprehenderit in voluptate velit esse cillum dolore eu fugiat nulla pariatur. Excepteur sint occaecat cupidatat non proident, sunt in culpa qui officia deserunt mollit anim id est laborum.Neque porro adipisci velit, sed quia non numquam eius modi tempora incidunt ut labore et dolore magnam aliquam quaerat voluptatem.</p>
<a class="btn about-btn abs">Read More</a>

<section class="services abs" role="img" aria-label="Purple tinted photo of a therapy session"></section>
<h2 class="section-title services-title abs">Our Services</h2>
<div class="kicker services-kicker abs">What We Do</div>
<div class="services-divider abs"></div>
<p class="services-copy abs">Lorem ipsum dolor sit amet, consectetur adipiscing elit, sed do eiusmod tempor incididunt ut labore et dolore magna aliqua. Ut enim ad minim veniam, quis nostrud exercitation ullamco laboris nisi ut aliquip ex ea commodo consequat.</p>

<article class="card abs" style="left:98px">
  <div class="card-icon" role="img" aria-label="Children icon"></div>
  <h3 class="card-title">Children</h3><hr>
  <p class="card-text">Lorem ipsum dolor sit amet, consectetur adipiscing elit, sed do eiusmod tempor incididunt ut labore et .</p>
  <a class="card-link">Read More <svg width="14" height="14" viewBox="0 0 14 14"><path d="M1 7h10M7 2l5 5-5 5" stroke="#141414" stroke-width="2.5" fill="none"/></svg></a>
</article>
<article class="card abs" style="left:442px">
  <div class="card-icon" role="img" aria-label="Adolescent icon"></div>
  <h3 class="card-title">Adolescents</h3><hr>
  <p class="card-text">Lorem ipsum dolor sit amet, consectetur adipiscing elit, sed do eiusmod tempor incididunt ut labore et .</p>
  <a class="card-link">Read More <svg width="14" height="14" viewBox="0 0 14 14"><path d="M1 7h10M7 2l5 5-5 5" stroke="#141414" stroke-width="2.5" fill="none"/></svg></a>
</article>
<article class="card abs" style="left:785px">
  <div class="card-icon" role="img" aria-label="Family icon"></div>
  <h3 class="card-title">Families</h3><hr>
  <p class="card-text">Lorem ipsum dolor sit amet, consectetur adipiscing elit, sed do eiusmod tempor incididunt ut labore et .</p>
  <a class="card-link">Read More <svg width="14" height="14" viewBox="0 0 14 14"><path d="M1 7h10M7 2l5 5-5 5" stroke="#141414" stroke-width="2.5" fill="none"/></svg></a>
</article>

<h2 class="section-title fees-title abs">Fees and Information</h2>
<div class="kicker fees-kicker abs">Consultation</div>
<p class="fees-copy abs">Lorem ipsum dolor sit amet, consectetur adipiscing elit, sed do eiusmod tempor incididunt ut labore et dolore magna aliqua. Ut enim ad minim veniam, quis nostrud exercitation ullamco laboris nisi ut aliquip ex ea commodo consequat.</p>
<div class="fees-photo abs" role="img" aria-label="Photo of a psychologist working with a child at a table with pencils"></div>
<div class="fees-panel abs">
  <h3>Fees and Information</h3>
  <ul class="fees-list">
    <li>Lorem ipsum dolor sit amet</li>
    <li>Duis aute irure dolor reprehenderit</li>
    <li>Excepteur sint occaecat cupidatat</li>
    <li>Sed ut perspiciatis unde omnis</li>
    <li>Nemo enim ipsam voluptatem</li>
  </ul>
</div>

<footer class="footer abs"></footer>
<div class="quick abs">
  <h4>Quick Links</h4>
  <ul>
    <li><svg width="14" height="14" viewBox="0 0 14 14"><path d="M1 7h10M7 2l5 5-5 5" stroke="#fff" stroke-width="2.5" fill="none"/></svg>Home</li>
    <li><svg width="14" height="14" viewBox="0 0 14 14"><path d="M1 7h10M7 2l5 5-5 5" stroke="#fff" stroke-width="2.5" fill="none"/></svg>About us</li>
    <li><svg width="14" height="14" viewBox="0 0 14 14"><path d="M1 7h10M7 2l5 5-5 5" stroke="#fff" stroke-width="2.5" fill="none"/></svg>Services</li>
    <li><svg width="14" height="14" viewBox="0 0 14 14"><path d="M1 7h10M7 2l5 5-5 5" stroke="#fff" stroke-width="2.5" fill="none"/></svg>Fees and information</li>
    <li><svg width="14" height="14" viewBox="0 0 14 14"><path d="M1 7h10M7 2l5 5-5 5" stroke="#fff" stroke-width="2.5" fill="none"/></svg>Contact Us</li>
  </ul>
</div>
<div class="social abs"><span></span><span></span><span></span><span></span></div>
<div class="vline abs" style="left:302px"></div>
<div class="contact abs">
  <h4>Contact Details</h4>
  <div class="contact-item">
    <span class="contact-icon"><svg width="14" height="14" viewBox="0 0 24 24"><path d="M6.6 10.8a15 15 0 006.6 6.6l2.2-2.2a1 1 0 011-.25 11 11 0 003.6.6 1 1 0 011 1V20a1 1 0 01-1 1A17 17 0 013 4a1 1 0 011-1h3.5a1 1 0 011 1 11 11 0 00.6 3.6 1 1 0 01-.25 1z" fill="#fff"/></svg></span>
    <div><b>Phone;</b><p>+61 2 5550 0142</p></div>
  </div>
  <div class="contact-item">
    <span class="contact-icon"><svg width="14" height="12" viewBox="0 0 14 12"><rect x="0" y="1" width="14" height="10" rx="1" fill="#fff"/><path d="M0 2l7 5 7-5" stroke="var(--plum)" stroke-width="1.5" fill="none"/></svg></span>
    <div><b>Email:</b><p>hello@clarawebb.example</p></div>
  </div>
  <div class="contact-item">
    <span class="contact-icon"><svg width="12" height="16" viewBox="0 0 12 16"><path d="M6 0a6 6 0 00-6 6c0 4.5 6 10 6 10s6-5.5 6-10a6 6 0 00-6-6z" fill="#fff"/><circle cx="6" cy="6" r="2.2" fill="var(--plum)"/></svg></span>
    <div><b>Address:</b><p>Clinical psychology practice in NSW Australia.</p></div>
  </div>
</div>
<div class="vline abs" style="left:670px"></div>
<div class="form abs">
  <h4>Contact Me</h4>
  <div class="field">Name:</div>
  <div class="field">Email:</div>
  <div class="field">Address:</div>
  <div class="submit">Submit Now</div>
</div>
<div class="footer-rule abs"></div>
<p class="copyright abs" style="color:#fff">Copyrights@2023. Dr.Clara Webb .All Rights Reserved</p>

</body>
</html>
```